New Business Card Design Project

Use the flyer uploaded and website www.brightoakbuilders.com for inspiration.
List Our Services on Backside of business cards
Marcus Delling
Harborline Builders Inc.
Licensed General Contractors
858-471-6093

Contact Information for Business Card

Use the flyer uploaded and website www.brightoakbuilders.com for inspiration. List Our Services on Backside of business cards Marcus Delling Harborline Builders Inc. Licensed General Contractors 858-471-6093

```html
<!DOCTYPE html>
<html lang="en">
<head>
<meta charset="utf-8">
<title>Harborline Builders – Business Card</title>
<link rel="stylesheet" href="https://fonts.googleapis.com/css2?family=Libre+Baskerville:ital,wght@0,400;0,700;1,700&display=swap">
<style>
  :root {
    --bg: #3b3b3d;
    --card: #0b0b0b;
    --ink: #f4f4f4;
    --accent: #2a8fd6;
    --band: #ffffff;
    --band-ink: #111111;
    --rule: #bdbdbd;
  }
  * { box-sizing: border-box; margin: 0; padding: 0; }
  html, body { width: 1200px; height: 900px; overflow: hidden; }
  body {
    background: var(--bg);
    font-family: "Libre Baskerville", Georgia, serif;
    color: var(--ink);
    position: relative;
  }
  .card {
    position: absolute;
    left: 250px;
    width: 700px;
    height: 400px;
    background: var(--card);
    box-shadow: 0 10px 28px rgba(0,0,0,.45);
    overflow: hidden;
  }
  .card--back { top: 30px; }
  .card--front { top: 470px; }

  .brand {
    position: absolute;
    left: 0; right: 0;
    display: flex;
    justify-content: center;
    align-items: center;
    gap: 12px;
  }
  .brand__mark { width: 12px; height: 12px; background: var(--ink); }
  .brand__name {
    font-size: 22px;
    font-weight: 400;
    letter-spacing: 2px;
    text-transform: uppercase;
    color: var(--ink);
  }
  .card--back .brand { top: 40px; }
  .card--front .brand { top: 110px; }
  .card--front .brand__name { font-size: 30px; letter-spacing: 3px; }
  .card--front .brand__mark { width: 16px; height: 16px; }

  .services__title {
    position: absolute;
    top: 92px; left: 0; right: 0;
    text-align: center;
    color: var(--accent);
    font-size: 18px;
    text-transform: uppercase;
  }
  .services__list {
    position: absolute;
    top: 126px; left: 0; right: 0;
    list-style: none;
    text-align: center;
    font-size: 15.5px;
    line-height: 27px;
  }
  .services__list .sep { color: var(--accent); padding: 0 6px; }

  .band {
    position: absolute;
    left: 0; right: 0;
    top: 308px;
    height: 48px;
    background: var(--band);
    border-top: 2px solid var(--accent);
    border-bottom: 2px solid var(--accent);
    color: var(--band-ink);
    display: flex;
    align-items: center;
    justify-content: center;
    font-size: 17px;
  }
  .band--guarantee { letter-spacing: 3px; }

  .holder {
    position: absolute;
    right: 390px; top: 250px;
    text-align: right;
    white-space: nowrap;
    font-size: 22px;
    font-weight: 700;
    letter-spacing: 1px;
    text-transform: uppercase;
  }
  .divider {
    position: absolute;
    left: 335px; top: 195px;
    width: 1px; height: 95px;
    background: var(--rule);
  }
  .contact {
    position: absolute;
    left: 365px; top: 198px;
  }
  .contact__cta {
    font-style: italic;
    font-weight: 700;
    font-size: 19px;
    margin-bottom: 10px;
  }
  .contact__row {
    display: flex;
    align-items: center;
    gap: 10px;
    font-size: 16px;
    line-height: 28px;
  }
  .contact__row svg { width: 18px; height: 18px; flex: none; }
</style>
</head>
<body>

  <section class="card card--back" aria-label="Card back – services">
    <div class="brand">
      <span class="brand__mark"></span>
      <span class="brand__name">Harborline Builders</span>
    </div>
    <h2 class="services__title">Our Services</h2>
    <ul class="services__list">
      <li>Remodel - Kitchen &amp; Bath<span class="sep">|</span>Painting - Interior &amp; Exterior</li>
      <li>Flooring - Carpet, Vinyl, Wood<span class="sep">|</span>Window &amp; Door Replacement</li>
      <li>Plumbing - Repairs &amp; Upgrades<span class="sep">|</span>Energy - Efficient Upgrades</li>
      <li>Deck &amp; Patio Construction<span class="sep">|</span>Water &amp; Mold Damage</li>
      <li>Garage Renovation</li>
    </ul>
    <div class="band band--guarantee">Our Services Are 100% Guaranteed</div>
  </section>

  <section class="card card--front" aria-label="Card front – contact">
    <div class="brand">
      <span class="brand__mark"></span>
      <span class="brand__name">Harborline Builders</span>
    </div>
    <p class="holder">Marcus Delling</p>
    <span class="divider"></span>
    <div class="contact">
      <p class="contact__cta">Call/Text Or Book Online</p>
      <p class="contact__row">
        <svg viewBox="0 0 24 24" aria-hidden="true"><path fill="none" stroke="#f4f4f4" stroke-width="2" d="M6 3l3 0 2 5-2 1.5c1 2.5 3 4.5 5.5 5.5L16 13l5 2v3c0 1.5-1 3-3 3C10 20 4 14 3 6c0-2 1.5-3 3-3z"/></svg>
        858-471-6093
      </p>
      <p class="contact__row">
        <svg viewBox="0 0 24 24" aria-hidden="true"><g fill="none" stroke="#f4f4f4" stroke-width="1.6"><circle cx="12" cy="12" r="9"/><ellipse cx="12" cy="12" rx="4" ry="9"/><path d="M3 12h18M5 7h14M5 17h14"/></g></svg>
        www.brightoakbuilders.com
      </p>
    </div>
    <div class="band">Harborline Builders Inc. - Licensed General Contractors</div>
  </section>

</body>
</html>
```